New business stationairy

I need paper with header and footer and business cards.
I am a Ltd Company and my main field of expertise is QA/QC inspection in the Oil and Gas Industry. I will need all contact detail inserted and a footer with registration number and bank details etc

```html
<!DOCTYPE html>
<html lang="en">
<head>
<meta charset="utf-8">
<title>Harlow Inspection Services – Business Cards</title>
<link rel="stylesheet" href="https://fonts.googleapis.com/css2?family=Oswald:wght@500&family=Questrial&family=Montserrat:wght@700&display=swap">
<style>
  :root {
    --navy: #2e2a78;
    --navy-deep: #221e5e;
    --gold: #d4a533;
    --white: #ffffff;
    --paper: #f4f4f2;
    --backdrop: #3a3a3c;
  }
  * { margin: 0; padding: 0; box-sizing: border-box; }
  html, body { width: 1200px; height: 900px; overflow: hidden; }
  body { background: var(--backdrop); position: relative; }

  .card {
    position: absolute;
    width: 700px;
    height: 400px;
    overflow: hidden;
    box-shadow: 0 14px 34px rgba(0,0,0,0.45);
  }
  .card svg.card-art { position: absolute; inset: 0; width: 100%; height: 100%; }

  /* Back of card */
  .card-back { left: 60px; top: 50px; background: linear-gradient(160deg, var(--navy) 0%, var(--navy-deep) 100%); }
  .card-back .brand {
    position: absolute; left: 0; right: 0; top: 70px;
    display: flex; align-items: center; justify-content: center; gap: 14px;
  }
  .brand-square { width: 34px; height: 34px; background: var(--gold); }
  .card-back .brand-name {
    font-family: "Oswald", sans-serif; font-weight: 500;
    font-size: 30px; letter-spacing: 1.5px; color: var(--white);
  }
  .card-back .address {
    position: absolute; left: 0; right: 0; top: 150px; text-align: center;
    font-family: "Questrial", sans-serif; font-size: 17px; line-height: 1.45;
    color: var(--white);
  }

  /* Front of card */
  .card-front { left: 440px; top: 460px; background: var(--paper); }
  .card-front .brand {
    position: absolute; right: 60px; top: 48px;
    display: flex; align-items: center; gap: 16px;
  }
  .card-front .brand-name {
    font-family: "Oswald", sans-serif; font-weight: 500;
    font-size: 30px; line-height: 1.0; letter-spacing: 1px;
    color: var(--navy); text-align: right; text-transform: uppercase;
  }
  .card-front .brand-square { width: 56px; height: 56px; }
  .holder {
    position: absolute; right: 40px; top: 200px; text-align: right;
  }
  .holder-name {
    font-family: "Montserrat", sans-serif; font-weight: 700;
    font-size: 26px; letter-spacing: 1px; color: var(--gold);
  }
  .holder-title {
    font-family: "Questrial", sans-serif; font-size: 18px;
    color: var(--white); margin-top: 4px;
  }
  .contacts {
    position: absolute; left: 40px; top: 298px; list-style: none;
    font-family: "Questrial", sans-serif; font-size: 16px; color: var(--white);
  }
  .contacts li { display: flex; align-items: center; gap: 10px; height: 26px; }
  .contacts svg { width: 18px; height: 18px; flex: none; }
</style>
</head>
<body>

  <section class="card card-back" aria-label="Business card, back">
    <svg class="card-art" viewBox="0 0 700 400" aria-hidden="true">
      <path d="M0,352 C260,330 500,250 700,128" fill="none" stroke="#d4a533" stroke-width="5"/>
      <path d="M0,368 C270,350 510,268 700,150 L700,200 C520,300 280,370 0,388 Z" fill="#d4a533"/>
    </svg>
    <div class="brand">
      <span class="brand-square"></span>
      <span class="brand-name">HARLOW INSPECTION SERVICES</span>
    </div>
    <p class="address">The Willows, Mill Lane, Ashcombe<br>Marlow Vale, Dorset, DT4 9QX</p>
  </section>

  <section class="card card-front" aria-label="Business card, front">
    <svg class="card-art" viewBox="0 0 700 400" aria-hidden="true">
      <path d="M0,262 C260,255 500,180 700,112 L700,400 L0,400 Z" fill="#2e2a78"/>
      <path d="M0,250 C260,244 500,168 700,96 L700,104 C500,180 260,254 0,258 Z" fill="#d4a533"/>
      <path d="M0,262 L700,262" stroke="none"/>
      <path d="M218,258 L242,258 L230,272 Z" fill="#d4a533"/>
    </svg>
    <div class="brand">
      <span class="brand-name">Harlow<br>Inspection<br>Services</span>
      <span class="brand-square"></span>
    </div>
    <div class="holder">
      <p class="holder-name">HELEN MARSH</p>
      <p class="holder-title">Managing Director</p>
    </div>
    <ul class="contacts">
      <li>
        <svg viewBox="0 0 18 18" aria-hidden="true"><circle cx="9" cy="9" r="8" fill="none" stroke="#d4a533" stroke-width="1.5"/><rect x="6.5" y="4" width="5" height="10" rx="1" fill="#d4a533"/></svg>
        +07700 900417
      </li>
      <li>
        <svg viewBox="0 0 18 18" aria-hidden="true"><circle cx="9" cy="9" r="8" fill="none" stroke="#d4a533" stroke-width="1.5"/><path d="M5.5,5 L7.5,4.5 L8.5,7 L7.3,8 C7.8,9.3 8.7,10.2 10,10.7 L11,9.5 L13.5,10.5 L13,12.5 C9,12.5 5.5,9 5.5,5 Z" fill="#d4a533"/></svg>
        +07700 900417
      </li>
      <li>
        <svg viewBox="0 0 18 18" aria-hidden="true"><circle cx="9" cy="9" r="8" fill="none" stroke="#d4a533" stroke-width="1.5"/><rect x="4.5" y="6" width="9" height="6.5" fill="#d4a533"/><path d="M4.5,6 L9,9.5 L13.5,6" fill="none" stroke="#2e2a78" stroke-width="1"/></svg>
        hmarsh@mailbox.co.uk
      </li>
    </ul>
  </section>

</body>
</html>
```